VelkaVision.com

Complete Website Design (Godaddy) and company Branding / Logo Design. The products will sell are only done in-person and are installed. So this site does not need to be an e-commerce site. We will only be giving out information and collecting customer inquires. Website will only need to be about 3 to 5 pages.

```html
<!DOCTYPE html>
<html lang="en">
<head>
<meta charset="utf-8">
<title>Velka Vision</title>
<link href="https://fonts.googleapis.com/css2?family=Poppins:wght@400;500;600;700;800&family=Mulish:wght@400;500;600&display=swap" rel="stylesheet">
<style>
:root{
  --orange:#f47a20;
  --orange-light:#f9a23a;
  --ink:#111111;
  --body:#2b2b2b;
  --muted:#8a8a8a;
  --panel:#ebebed;
  --white:#ffffff;
  --black:#050505;
}
*{box-sizing:border-box;margin:0;padding:0}
html,body{width:1200px;height:2487px;overflow:hidden}
body{font-family:"Mulish",sans-serif;color:var(--body);background:var(--white);position:relative}
.btn{display:inline-flex;align-items:center;gap:10px;background:linear-gradient(180deg,var(--orange-light),var(--orange));color:var(--white);border-radius:3px;font-weight:600}
.brand{display:flex;align-items:center;gap:10px;font-family:"Poppins",sans-serif;font-weight:700}
.brand-mark{width:30px;height:30px;border:3px solid var(--orange);border-radius:6px}

/* header */
.site-header{position:absolute;top:0;left:0;width:1200px;height:86px;display:flex;align-items:center;padding:0 97px;box-shadow:0 2px 8px rgba(0,0,0,.08);background:var(--white);z-index:2}
.site-header .brand{font-size:27px;color:var(--ink)}
.main-nav{margin-left:auto;display:flex;gap:33px;font-family:"Poppins",sans-serif;font-size:16px;color:var(--ink)}
.main-nav .active{color:var(--orange);font-weight:600}
.header-phone{margin-left:20px;height:47px;padding:0 13px;font-family:"Poppins",sans-serif;font-size:16px}

/* hero */
.hero{position:absolute;top:86px;left:0;width:1200px;height:562px;background:linear-gradient(90deg,#e4e5e7 0%,#eceded 40%,#dcdde0 100%)}
.hero-photo{position:absolute;right:0;top:0;width:700px;height:562px;background:radial-gradient(ellipse at 55% 45%,#8a8a8a 0%,#c9cacc 45%,rgba(225,226,228,0) 75%)}
.hero-copy{position:absolute;left:97px;top:118px;width:370px}
.hero h1{font-family:"Poppins",sans-serif;font-weight:800;font-size:55px;line-height:76px;color:var(--ink)}
.hero p{margin-top:14px;font-size:15.5px;line-height:31px;color:var(--ink)}
.hero .btn{margin-top:20px;height:47px;padding:0 18px;font-size:16px}

/* about */
.about-frame{position:absolute;left:240px;top:870px;width:342px;height:285px;background:linear-gradient(180deg,var(--orange-light),var(--orange))}
.about-photo{position:absolute;left:116px;top:765px;width:450px;height:377px;background:linear-gradient(135deg,#d9d9e6 0%,#c3c4d4 50%,#d9c2a6 100%)}
.about-copy{position:absolute;left:651px;top:748px;width:450px}
.about-copy h2{font-family:"Poppins",sans-serif;font-weight:700;font-size:33px;color:var(--ink)}
.about-copy p{margin-top:18px;font-size:15.5px;line-height:28.3px;color:var(--ink)}
.about-copy .btn{margin-top:23px;height:47px;padding:0 17px;font-size:16px}

/* contact */
.contact{position:absolute;top:1252px;left:2px;width:1198px;height:788px;background:linear-gradient(125deg,#e7e7e9 0%,#f1f1f2 30%,#e4e4e6 55%,#efeff0 80%,#e9e9eb 100%)}
.contact h2{position:absolute;top:50px;width:100%;text-align:center;font-family:"Poppins",sans-serif;font-weight:700;font-size:33px;color:var(--ink)}
.info-row{position:absolute;top:120px;left:176px;display:flex;gap:0}
.info-item{display:flex;align-items:center;gap:12px;font-size:16.5px;color:var(--ink);font-weight:500}
.info-icon{width:44px;height:44px;border-radius:50%;background:linear-gradient(180deg,var(--orange-light),var(--orange));display:flex;align-items:center;justify-content:center}
.map{position:absolute;left:102px;top:210px;width:461px;height:490px;border-radius:18px;background:linear-gradient(160deg,#cfd9c3 0%,#dcd8c8 40%,#c4d6b5 75%,#d6d3c4 100%)}
.enquiry-form{position:absolute;left:593px;top:211px;width:507px}
.field{width:100%;height:60px;background:var(--white);border:1px solid #d5d5d5;border-radius:5px;box-shadow:0 3px 5px rgba(0,0,0,.18);padding:0 32px;display:flex;align-items:center;font-family:"Poppins",sans-serif;font-size:15.5px;color:var(--muted);margin-bottom:27px}
.field.message{height:146px;align-items:flex-start;padding-top:28px;margin-bottom:27px}
.submit{height:51px;width:196px;justify-content:center;font-family:"Poppins",sans-serif;font-size:17px;border-radius:2px}

/* footer */
.site-footer{position:absolute;top:2040px;left:0;width:1200px;height:447px;background:var(--black);color:var(--white)}
.site-footer .brand{position:absolute;top:95px;left:0;width:100%;justify-content:center;font-size:28px}
.footer-nav{position:absolute;top:172px;width:100%;display:flex;justify-content:center;gap:32px;font-size:16px;font-weight:500}
.footer-contacts{position:absolute;top:233px;left:170px;width:910px;display:flex;justify-content:space-between}
.fc{display:flex;align-items:center;gap:21px;font-size:16px}
.fc-icon{width:49px;height:49px;background:linear-gradient(180deg,var(--orange-light),var(--orange));display:flex;align-items:center;justify-content:center}
.copyright{position:absolute;top:335px;width:100%;text-align:center;font-size:17px;font-weight:500}
.copyright span{color:var(--orange)}
</style>
</head>
<body>

<header class="site-header">
  <div class="brand"><span class="brand-mark"></span>Velka Vision</div>
  <nav class="main-nav">
    <span class="active">Home</span><span>About Us</span><span>Services</span><span>Blog</span><span>Contact Us</span>
  </nav>
  <span class="btn header-phone">
    <svg width="16" height="16" viewBox="0 0 24 24"><path fill="#fff" d="M6.6 10.8a15 15 0 006.6 6.6l2.2-2.2c.3-.3.7-.4 1-.2 1.1.4 2.3.6 3.6.6.6 0 1 .4 1 1V20c0 .6-.4 1-1 1A17 17 0 013 4c0-.6.4-1 1-1h3.5c.6 0 1 .4 1 1 0 1.3.2 2.5.6 3.6.1.3 0 .7-.2 1z"/></svg>
    +1 555 0142 0199
  </span>
</header>

<section class="hero">
  <div class="hero-photo" role="img" aria-label="Two technicians mounting a large flat TV on a white wall between speakers"></div>
  <div class="hero-copy">
    <h1>Welcome To Velka Vision</h1>
    <p>Lorem ipsum dolor sit amet, consectetur adipiscing elit, sed do eiusmod tempor incididunt ut labore et dolore magna aliqua.</p>
    <span class="btn">Get Started
      <svg width="18" height="16" viewBox="0 0 18 16"><path d="M1 8h13M9 2l6 6-6 6" stroke="#fff" stroke-width="3" fill="none"/></svg>
    </span>
  </div>
</section>

<section class="about">
  <div class="about-frame"></div>
  <div class="about-photo" role="img" aria-label="Technician in blue overalls setting up a TV on a white media console"></div>
  <div class="about-copy">
    <h2>About Us</h2>
    <p>Lorem ipsum dolor sit amet, consectetur adipiscing elit, sed do eiusmod tempor incididunt ut labore et dolore magna aliqua. Ut enim ad minim veniam, quis nostrud exercitation ullamco laboris nisi ut aliquip ex ea commodo consequat. Duis aute irure dolor in reprehenderit in voluptate velit esse cillum dolore eu fugiat nulla pariatur. Excepteur sint occaecat cupidatat non proident, sunt in culpa qui officia deserunt mollit anim id est laborum.Sed ut ipsa quae ab illo inventore veritatis et quasi architecto beatae vitae dicta sunt explicabo.</p>
    <span class="btn">Read More
      <svg width="18" height="16" viewBox="0 0 18 16"><path d="M1 8h13M9 2l6 6-6 6" stroke="#fff" stroke-width="3" fill="none"/></svg>
    </span>
  </div>
</section>

<section class="contact">
  <h2>Contact Us</h2>
  <div class="info-row">
    <div class="info-item" style="width:262px">
      <span class="info-icon"><svg width="16" height="16" viewBox="0 0 24 24"><path fill="#fff" d="M6.6 10.8a15 15 0 006.6 6.6l2.2-2.2c.3-.3.7-.4 1-.2 1.1.4 2.3.6 3.6.6.6 0 1 .4 1 1V20c0 .6-.4 1-1 1A17 17 0 013 4c0-.6.4-1 1-1h3.5c.6 0 1 .4 1 1 0 1.3.2 2.5.6 3.6.1.3 0 .7-.2 1z"/></svg></span>+1 555 0142 0199
    </div>
    <div class="info-item" style="width:304px">
      <span class="info-icon"><svg width="16" height="12" viewBox="0 0 16 12"><rect width="16" height="12" rx="1" fill="#fff"/><path d="M1 1l7 5 7-5" stroke="#f47a20" stroke-width="1.5" fill="none"/></svg></span>info@velkavision.com
    </div>
    <div class="info-item">
      <span class="info-icon"><svg width="12" height="17" viewBox="0 0 12 17"><path fill="#fff" d="M6 0a6 6 0 016 6c0 4.5-6 11-6 11S0 10.5 0 6a6 6 0 016-6z"/><circle cx="6" cy="6" r="2.2" fill="#f47a20"/></svg></span>Velka Vision,United State.
    </div>
  </div>
  <div class="map" role="img" aria-label="Map of the central United States with a pin marking the office location"></div>
  <form class="enquiry-form">
    <div class="field">Enter Your Name</div>
    <div class="field">Enter Your Email Address</div>
    <div class="field" style="margin-top:6px">Phone Number</div>
    <div class="field message">Your Message</div>
    <span class="btn submit">Submit Enquiry</span>
  </form>
</section>

<footer class="site-footer">
  <div class="brand"><span class="brand-mark"></span>Velka Vision</div>
  <nav class="footer-nav"><span>HOME</span><span>ABOUT US</span><span>SERVICES</span><span>TESTIMONIALS</span><span>CONTACT US</span></nav>
  <div class="footer-contacts">
    <div class="fc"><span class="fc-icon"><svg width="24" height="18" viewBox="0 0 16 12"><rect width="16" height="12" rx="1" fill="#fff"/><path d="M1 1l7 5 7-5" stroke="#f47a20" stroke-width="1.5" fill="none"/></svg></span>info@VelkaVision.com</div>
    <div class="fc"><span class="fc-icon"><svg width="14" height="20" viewBox="0 0 12 17"><path fill="#fff" d="M6 0a6 6 0 016 6c0 4.5-6 11-6 11S0 10.5 0 6a6 6 0 016-6z"/><circle cx="6" cy="6" r="2.2" fill="#f47a20"/></svg></span>Velka Vision ,United State.</div>
    <div class="fc"><span class="fc-icon"><svg width="22" height="22" viewBox="0 0 24 24"><path fill="#fff" d="M6.6 10.8a15 15 0 006.6 6.6l2.2-2.2c.3-.3.7-.4 1-.2 1.1.4 2.3.6 3.6.6.6 0 1 .4 1 1V20c0 .6-.4 1-1 1A17 17 0 013 4c0-.6.4-1 1-1h3.5c.6 0 1 .4 1 1 0 1.3.2 2.5.6 3.6.1.3 0 .7-.2 1z"/></svg></span>+1 555 0142 0199</div>
  </div>
  <p class="copyright">Copyrights@2024.<span>Velka Vision</span>.All Rights Reserved</p>
</footer>

</body>
</html>
```